Life Coaching business needs a new flyer

We are an Australian business that specialises in Life Coaching, Career Coaching, Health and Wellness Coaching, Yoga and Pilates. We need a A4 double sided flyer that is full colour and folded to DL format. I have attached a couple of designs that I like and some pictures and would like the flyer to be bright yet stylish.

Industry/Entity Type

Life Coaching

```html
<!DOCTYPE html>
<html lang="en">
<head>
<meta charset="utf-8">
<title>Clearpath Coaching – DL Brochure</title>
<link href="https://fonts.googleapis.com/css2?family=Noto+Serif:wght@400;700&family=PT+Sans:ital,wght@0,400;0,700;1,400&family=Lobster+Two:ital,wght@1,700&display=swap" rel="stylesheet">
<style>
:root{
  --backdrop:#b9b9b9;
  --blue:#3f6fb3;
  --blue-light:#5a92d0;
  --green:#52b800;
  --teal:#1a93c9;
  --ink:#222;
  --grey:#555;
  --white:#fff;
  --serif:"Noto Serif",Georgia,serif;
  --sans:"PT Sans",Arial,sans-serif;
  --script:"Lobster Two",cursive;
}
*{box-sizing:border-box;margin:0;padding:0}
html,body{width:874px;height:1200px;overflow:hidden}
body{background:var(--backdrop);position:relative;font-family:var(--sans);color:var(--ink)}
.sheet{position:absolute;left:69px;width:705px;height:498px;display:flex;box-shadow:0 1px 4px rgba(0,0,0,.25);background:var(--white)}
.sheet--outside{top:75px}
.sheet--inside{top:626px;display:block}
.panel{width:235px;height:100%;position:relative;overflow:hidden}
.photo{position:absolute;left:0;right:0;bottom:0}

/* testimonials */
.panel--testimonials{background:linear-gradient(180deg,var(--blue) 0%,var(--blue-light) 100%);color:var(--white);padding:20px 32px 0 25px}
.panel--testimonials h2{font-family:var(--serif);font-weight:400;font-size:13px;margin-bottom:5px}
.quote{font-size:7.2px;line-height:1.33;text-align:justify;margin-bottom:9px}
.panel--testimonials .photo{height:166px;background:linear-gradient(180deg,#4d8fd6 0%,#8fc3ef 55%,#e6a07c 100%)}

/* contact */
.panel--contact{background:var(--green);color:var(--white);padding:24px 26px 0}
.intro{font-size:6.8px;line-height:1.4;margin-bottom:9px}
.contact-box{margin-top:14px;background:linear-gradient(180deg,#3aa8ea,#1380cf);border:1.5px solid #7cc6f3;border-radius:6px;padding:4px 9px 5px;font-family:var(--serif)}
.contact-box h3{font-size:13px;font-weight:700;margin-bottom:3px}
.contact-box p{font-size:8.3px;font-weight:700;line-height:1.5}
.brand{text-align:center;margin-top:26px}
.brand-dot{width:64px;height:64px;border-radius:50%;border:3px solid var(--white);margin:0 auto 6px}
.brand-name{font-family:var(--serif);font-size:14px;font-weight:400;line-height:1.2}
.panel--contact .offer{font-family:var(--serif);font-weight:700;font-size:9.6px;text-align:center;line-height:1.45;margin-top:22px;white-space:nowrap;margin-left:-10px;margin-right:-10px}
.panel--contact .photo{height:149px;background:linear-gradient(180deg,#5e8a2a 0%,#7c6a55 40%,#3b3936 100%)}

/* cover */
.panel--cover .hero{position:absolute;top:0;left:0;width:235px;height:260px}
.cover-brand{position:absolute;top:228px;left:0;right:0;text-align:center}
.cover-brand .brand-dot{border-color:var(--green)}
.cover-brand .brand-name{color:var(--teal);font-size:15px}
.cover-title{position:absolute;top:350px;left:0;right:0;text-align:center;font-family:var(--script);font-style:italic;font-weight:700;color:var(--teal);font-size:31px;line-height:38px}

/* inside */
.columns{display:flex;height:401px}
.col{width:235px;padding:14px 32px 0 25px;font-size:8.8px;line-height:1.3;color:var(--grey)}
.col--services{padding:14px 35px 0 22px}
.col h3{font-family:var(--serif);font-weight:400;color:var(--teal);font-size:13.5px;line-height:1.25;margin:6px 0 2px}
.col p{margin-bottom:8px}
.col .justify{text-align:justify}
.questions{padding-top:4px}
.questions p{color:var(--ink);font-weight:700;font-size:8.7px;line-height:1.3;margin-bottom:6px}
.questions p.gap{margin-top:11px}
.mission p{font-size:10px;line-height:1.3;margin-bottom:12px}
.needs{list-style:none;margin:14px 0 10px}
.needs li{font-style:italic;display:flex;align-items:flex-start;gap:5px;margin-bottom:1.8px}
.needs svg{flex:none;margin-top:1px}
.strip{display:flex;height:97px}
.strip div{flex:1}
.strip-hiker{background:linear-gradient(180deg,#9fb2c4 0%,#d9e0e4 55%,#8d8a78 100%)}
.strip-class{background:linear-gradient(180deg,#5da7e2 0%,#9fd0ee 50%,#7cb14a 100%)}
.strip-sail{background:linear-gradient(180deg,#3f7fc9 0%,#8ec0ea 60%,#f1f4f6 100%)}
</style>
</head>
<body>

<section class="sheet sheet--outside">
  <div class="panel panel--testimonials">
    <h2>Happy Clients Testimonials</h2>
    <p class="quote">“I have lost 10 kilos and now have the energy to play with my kids. Thanks Mara for your support/guidance and helping me get rid of my limiting beliefs. I feel I can achieve anything now! The sky’s the limit” Dana, Mosman</p>
    <p class="quote">“I had always wanted to start up own café however every time it came to putting it into practice I would procrastinate and not achieve anything. I became overwhelmed with the whole process and never achieved anything. Mara put it into bite sized chunks and helped me to set small achievable goals. I am now a happy café owner.” Elise, Double Bay</p>
    <p class="quote">“Mara has helped to change my life around in all aspects. I would have been lost without her. Thanks Mara for your professionalism, support and guidance.” Rosa, Cremorne</p>
    <p class="quote">“I was so busy with kids, work, and my husband I lost who I was. Mara has helped me find the person I am again.” Tessa, Chatswood</p>
    <p class="quote">“When I started with Coach Mara, I didn’t know anything about coaching. I called her because she helped a friend of mine make a career change that was a perfect fit for her. I had the opportunity to make a change too and did not know where to start. I am now in a job that I love. I would recommend Mara to everyone.” Owen, Texas America</p>
    <div class="photo" role="img" aria-label="Photo of four happy young friends jumping with arms raised against a blue sky"></div>
  </div>

  <div class="panel panel--contact">
    <p class="intro">Clearpath Coaching and Meditation Centre is a professional service that can help you achieve the goals that you are looking for in Life Coaching, Meditation, and Yoga/Pilates.</p>
    <p class="intro">If you are ready to take your life to the next level and would like to know more, please</p>
    <div class="contact-box">
      <h3>contact us.</h3>
      <p>Phone : 02 5550 1234</p>
      <p>info@clearpathcoaching.com.au</p>
      <p>www.clearpathcoaching.com.au</p>
    </div>
    <div class="brand">
      <div class="brand-dot"></div>
      <p class="brand-name">Clearpath Coaching</p>
    </div>
    <p class="offer">Free Introductory Life Coaching<br>Phone/Video session - 20 mins<br>(To see if coaching is right for you)</p>
    <div class="photo" role="img" aria-label="Portrait photo of the two coaches, a woman and a man"></div>
  </div>

  <div class="panel panel--cover">
    <svg class="hero" viewBox="0 0 235 260" role="img" aria-label="Photo of a woman in a yoga balance pose beside a blue pool under a clear sky">
      <defs>
        <linearGradient id="heroSky" x1="0" y1="0" x2="0" y2="1">
          <stop offset="0" stop-color="#7fcdf2"/>
          <stop offset=".45" stop-color="#3aa7dc"/>
          <stop offset="1" stop-color="#1585c4"/>
        </linearGradient>
      </defs>
      <rect width="235" height="260" fill="url(#heroSky)"/>
      <path d="M0 142 C80 146 170 182 235 255 L235 260 L0 260 Z" fill="#fff"/>
      <path d="M45 150 C125 156 195 192 235 256" fill="none" stroke="var(--green)" stroke-width="5"/>
    </svg>
    <div class="cover-brand">
      <div class="brand-dot"></div>
      <p class="brand-name">Clearpath Coaching</p>
    </div>
    <p class="cover-title">Life Coaching<br>Meditation<br>Yoga/Pilates</p>
  </div>
</section>

<section class="sheet sheet--inside">
  <div class="columns">
    <div class="col">
      <div class="questions">
        <p>Are you looking at making changes this year?</p>
        <p>Are you stuck in a rut or at a crossroad in your life?</p>
        <p>Are you wanting to lose weigh but can’t get motivated?</p>
        <p class="gap">Do you have ongoing problems with your career, relationships, or just life itself?</p>
        <p>Life coaching is the answer</p>
      </div>
      <h3>Clearpath Coaching and Meditation Centre</h3>
      <div class="mission">
        <p class="justify">Our mission is to help you become the best possible person you can be. Mentally, physically, and spiritually.</p>
        <p class="justify">We offer highly qualified and compassionate trainers/coaches for Life Coaching, Meditation, Yoga and Pilates.</p>
        <p class="justify">They will guide and motivate you every step of the way to achieve all your dreams and goals.</p>
        <p>They will make you be the best you can be</p>
      </div>
    </div>

    <div class="col col--services">
      <h3>Life Coaching</h3>
      <p class="justify">Your Life Coach will give you the confidence and the ability to move forward in a positive manner in all areas of your life where you crave change.</p>
      <p class="justify">Life Coaching is about breaking down the barriers preventing this change from happening, and creating the ideal environment for positive action to take place. It is a holistic approach, which looks at the present and sets goals for a totally successful future.</p>
      <h3>Career Coaching</h3>
      <p class="justify">Are you at a crossroads in your career and at a loss about what to do next? Do you want your work to be in alignment with the authentic you? It can be difficult to assess career options, goals, and strategies, and have the confidence to implement changes on your own. With the right coaching support, you will gain the clarity that you need to take control and have a fulfilling and rewarding career.</p>
      <h3>Wellness Coaching</h3>
      <p class="justify">Health and wellness coaches help their clients find the motivation and tools to achieve their health and wellness goals, working with the client to examine and improve the psychological framework that supports those goals.</p>
    </div>

    <div class="col">
      <h3>Why Would I Need Help?</h3>
      <p>Coaching is for anyone who wants to make lasting changes in their life.</p>
      <p style="margin-top:12px">Coaching can assist with such issues as:</p>
      <ul class="needs">
        <li><svg width="9" height="9" viewBox="0 0 10 10"><circle cx="5" cy="5" r="4.5" fill="var(--green)"/><path d="M2.8 5.2 4.4 6.7 7.3 3.6" fill="none" stroke="#fff" stroke-width="1.3"/></svg>Creating a better work- life balance</li>
        <li><svg width="9" height="9" viewBox="0 0 10 10"><circle cx="5" cy="5" r="4.5" fill="var(--green)"/><path d="M2.8 5.2 4.4 6.7 7.3 3.6" fill="none" stroke="#fff" stroke-width="1.3"/></svg>Resolving relationship issues</li>
        <li><svg width="9" height="9" viewBox="0 0 10 10"><circle cx="5" cy="5" r="4.5" fill="var(--green)"/><path d="M2.8 5.2 4.4 6.7 7.3 3.6" fill="none" stroke="#fff" stroke-width="1.3"/></svg>Career guidance</li>
        <li><svg width="9" height="9" viewBox="0 0 10 10"><circle cx="5" cy="5" r="4.5" fill="var(--green)"/><path d="M2.8 5.2 4.4 6.7 7.3 3.6" fill="none" stroke="#fff" stroke-width="1.3"/></svg>Stress management</li>
        <li><svg width="9" height="9" viewBox="0 0 10 10"><circle cx="5" cy="5" r="4.5" fill="var(--green)"/><path d="M2.8 5.2 4.4 6.7 7.3 3.6" fill="none" stroke="#fff" stroke-width="1.3"/></svg>Weight loss and fitness</li>
        <li><svg width="9" height="9" viewBox="0 0 10 10"><circle cx="5" cy="5" r="4.5" fill="var(--green)"/><path d="M2.8 5.2 4.4 6.7 7.3 3.6" fill="none" stroke="#fff" stroke-width="1.3"/></svg>Motivation and goal setting</li>
        <li><svg width="9" height="9" viewBox="0 0 10 10"><circle cx="5" cy="5" r="4.5" fill="var(--green)"/><path d="M2.8 5.2 4.4 6.7 7.3 3.6" fill="none" stroke="#fff" stroke-width="1.3"/></svg>Boosting your self esteem</li>
        <li><svg width="9" height="9" viewBox="0 0 10 10"><circle cx="5" cy="5" r="4.5" fill="var(--green)"/><path d="M2.8 5.2 4.4 6.7 7.3 3.6" fill="none" stroke="#fff" stroke-width="1.3"/></svg>Overcoming negative emotions and thoughts</li>
        <li><svg width="9" height="9" viewBox="0 0 10 10"><circle cx="5" cy="5" r="4.5" fill="var(--green)"/><path d="M2.8 5.2 4.4 6.7 7.3 3.6" fill="none" stroke="#fff" stroke-width="1.3"/></svg>Better time management</li>
      </ul>
      <h3>Meditation</h3>
      <p>We specialise in teaching meditation from beginners to advanced and teach a variety of techniques for stress reduction, peace of mind, stillness, and clarity.</p>
      <h3>Yoga/Pilates</h3>
      <p class="justify">Your highly qualified and experienced Yoga or Pilates instructor will come to you and create a fun and varied workout based on what you enjoy and what your goals are.</p>
    </div>
  </div>
  <div class="strip">
    <div class="strip-hiker" role="img" aria-label="Photo of a hiker with a red backpack overlooking a mountain valley"></div>
    <div class="strip-class" role="img" aria-label="Photo of a group meditating cross-legged on mats outdoors"></div>
    <div class="strip-sail" role="img" aria-label="Photo of a smiling older couple on a sailing boat"></div>
  </div>
</section>

</body>
</html>
```